Business Card Design needed for start up company Halvora

In need of a new business card designed for a start up company based in Sydney, Halvora is a new start up innovative Company, our mission it to make property accessible for everyday Australian and to become the leading Real Estate platform in Australia. We want it to be fresh and clean.

Industry/Entity Type

Financial

Contact Information for Business Card

Section for Name
Section for Title

HALVORA - The Strength of Pooling
Mobile:
Direct:

Font styles to use
Sans Serif

Colors
33a6d7
0692cd
0255a3
ffffff

Requirements
Must have
• Logo, all business card details

```html
<!DOCTYPE html>
<html lang="en">
<head>
<meta charset="utf-8">
<title>Halvora Business Card</title>
<link rel="stylesheet" href="https://fonts.googleapis.com/css2?family=Exo+2:wght@400;500;700&display=swap">
<style>
  :root {
    --page-bg: #e9ebef;
    --brand-navy: #23449b;
    --brand-sky: #4dbbe8;
    --card-white: #ffffff;
    --rule-grey: #9a9a9a;
    --text-grey: #3c3c3c;
  }
  * { box-sizing: border-box; margin: 0; padding: 0; }
  html, body {
    width: 1200px;
    height: 1000px;
    overflow: hidden;
    background: var(--page-bg);
    font-family: "Exo 2", sans-serif;
  }
  .card {
    position: absolute;
    left: 250px;
    width: 700px;
    height: 400px;
    border-radius: 24px;
    box-shadow: 0 6px 18px rgba(0,0,0,0.15);
    overflow: hidden;
  }
  .card--front { top: 60px; background: var(--brand-navy); }
  .card--back { top: 540px; background: var(--card-white); }

  .wordmark {
    position: absolute;
    font-weight: 700;
    letter-spacing: 2px;
    line-height: 1;
  }
  .card--front .wordmark {
    left: 50%; top: 50%;
    transform: translate(-50%, -50%);
    font-size: 76px;
    color: var(--card-white);
  }
  .card--back .wordmark {
    left: 40px; top: 56px;
    font-size: 46px;
    color: var(--brand-navy);
  }

  .divider {
    position: absolute;
    left: 40px; top: 192px;
    width: 560px; height: 2px;
    background: var(--rule-grey);
  }
  .person {
    position: absolute;
    right: 40px; top: 200px;
    text-align: right;
  }
  .person__name {
    font-size: 30px;
    line-height: 36px;
    font-weight: 700;
    color: var(--brand-navy);
    letter-spacing: 1px;
    border-bottom: 2px solid var(--rule-grey);
  }
  .person__title {
    font-size: 22px;
    line-height: 28px;
    font-weight: 500;
    color: var(--brand-sky);
    letter-spacing: 1px;
  }
  .address {
    position: absolute;
    left: 40px; top: 292px;
    font-size: 18px;
    line-height: 1.35;
    color: var(--text-grey);
    letter-spacing: 1px;
  }
  .contacts {
    position: absolute;
    right: 40px; top: 278px;
    list-style: none;
  }
  .contacts li {
    display: flex;
    justify-content: flex-end;
    align-items: center;
    gap: 12px;
    height: 24px;
    font-size: 17px;
    color: var(--text-grey);
    letter-spacing: 1px;
  }
  .contacts .accent { color: var(--brand-navy); }
  .contacts svg { width: 19px; height: 19px; flex: none; }
</style>
</head>
<body>
  <section class="card card--front" aria-label="Card front">
    <div class="wordmark">HALVORA</div>
  </section>

  <section class="card card--back" aria-label="Card back">
    <div class="wordmark">HALVORA</div>
    <div class="divider"></div>
    <div class="person">
      <div class="person__name">DANA WHITLOW</div>
      <div class="person__title">Director</div>
    </div>
    <p class="address">Your Street Address,<br>Sydney, 2000</p>
    <ul class="contacts">
      <li>000 123 456 789
        <svg viewBox="0 0 20 20" aria-hidden="true"><circle cx="10" cy="10" r="10" fill="#23449b"/><path d="M7 5.5c.6-.4 1.2 0 1.4.5l.6 1.5c.2.5 0 .9-.4 1.2l-.5.4c.6 1.3 1.4 2.1 2.6 2.7l.4-.5c.3-.4.8-.5 1.2-.3l1.5.7c.5.2.8.8.4 1.4-.7 1-1.8 1.4-3 .9-2.3-1-3.8-2.6-4.7-4.8-.4-1.2 0-2.300.5-3.100z" fill="#fff"/></svg>
      </li>
      <li>000 222 3334
        <svg viewBox="0 0 20 20" aria-hidden="true"><circle cx="10" cy="10" r="10" fill="#23449b"/><rect x="7" y="4.5" width="6" height="11" rx="1" fill="none" stroke="#fff" stroke-width="1.3"/><circle cx="10" cy="13.5" r=".7" fill="#fff"/></svg>
      </li>
      <li>urname@email.com
        <svg viewBox="0 0 20 20" aria-hidden="true"><circle cx="10" cy="10" r="10" fill="#23449b"/><rect x="5" y="6.5" width="10" height="7" fill="none" stroke="#fff" stroke-width="1.3"/><path d="M5 6.5l5 4 5-4" fill="none" stroke="#fff" stroke-width="1.3"/></svg>
      </li>
      <li><span>www.<span class="accent">websitename</span>.com</span>
        <svg viewBox="0 0 20 20" aria-hidden="true"><circle cx="10" cy="10" r="10" fill="#23449b"/><g fill="none" stroke="#fff" stroke-width="1.1"><circle cx="10" cy="10" r="5.5"/><ellipse cx="10" cy="10" rx="2.3" ry="5.5"/><path d="M4.5 10h11M5.5 7h9M5.5 13h9"/></g></svg>
      </li>
    </ul>
  </section>
</body>
</html>
```